KBT Business Cards

We require business cards for our business. We would like a matte black back to the card, with our logo centred in the middle. The front side of the card is open to design.

Target Market(s)

Clients looking for legal services (professional)

Industry/Entity Type

Legal

Contact Information for Business Card

Doran Kelbrath
Partner
Mobile: 0461 738 524
Email: doran@kbtlaw.co
Website: www.kbtlaw.co
Level 3, 118 Wendmore Street
Sydney NSW 2000

Font styles to use
Other font styles liked:
• Avenir

Colors
f04a50
ffffff
1b1b1b

Requirements
Must have
• Black back with logo included in the centre of the card.
• Our font is Avenir.

```html
<!DOCTYPE html>
<html lang="en">
<head>
<meta charset="utf-8">
<title>KBT Business Cards</title>
<link href="https://fonts.googleapis.com/css2?family=Roboto:wght@400;500&display=swap" rel="stylesheet">
<style>
  :root {
    --backdrop: #e4e4e4;
    --card-white: #ffffff;
    --card-black: #231f20;
    --accent: #d4214d;
    --ink: #1b1b1b;
    --muted: #555555;
    --rule: #9a9a9a;
  }
  * { margin: 0; padding: 0; box-sizing: border-box; }
  html, body {
    width: 1125px; height: 1200px; overflow: hidden;
    background: var(--backdrop);
    font-family: "Roboto", "Helvetica Neue", Arial, sans-serif;
  }
  .canvas { position: relative; width: 1125px; height: 1200px; }
  .card {
    position: absolute; left: 171px; width: 826px; height: 471px;
  }
  .card--front { top: 105px; background: var(--card-white); }
  .card--back { top: 639px; background: var(--card-black); }

  .holder {
    position: absolute; right: 426px; top: 208px; text-align: right;
  }
  .holder__name {
    color: var(--accent); font-size: 29px; font-weight: 500; line-height: 1.15;
  }
  .holder__role {
    color: var(--ink); font-size: 20px; font-weight: 400; margin-top: 2px;
  }
  .divider {
    position: absolute; left: 431px; top: 153px; width: 1.5px; height: 168px;
    background: var(--rule);
  }
  .address {
    position: absolute; left: 461px; top: 153px;
    color: var(--muted); font-size: 19.5px; line-height: 25px; font-style: normal;
  }
  .contacts {
    position: absolute; left: 461px; top: 239px; list-style: none;
    color: var(--muted); font-size: 19.5px; line-height: 26.5px;
  }
  .contacts li { display: flex; align-items: center; }
  .contacts svg { width: 20px; height: 20px; margin-right: 12px; flex: none; }

  .brand {
    position: absolute; left: 50%; top: 50%; transform: translate(-50%, -50%);
    display: flex; align-items: center; gap: 30px;
  }
  .brand__mark { width: 54px; height: 54px; background: var(--accent); flex: none; }
  .brand__name {
    color: var(--card-white); font-size: 42px; font-weight: 500;
    line-height: 42px; letter-spacing: 0.5px;
  }
</style>
</head>
<body>
<main class="canvas">
  <section class="card card--front">
    <div class="holder">
      <p class="holder__name">Doran Kelbrath</p>
      <p class="holder__role">Partner</p>
    </div>
    <div class="divider"></div>
    <address class="address">
      Level 3, 118<br>Wendmore Street<br>Sydney NSW 2000
    </address>
    <ul class="contacts">
      <li>
        <svg viewBox="0 0 20 20" aria-hidden="true"><rect x="5" y="1.5" width="10" height="17" rx="1.5" fill="none" stroke="#d4214d" stroke-width="2"/><rect x="8.5" y="15" width="3" height="1.5" fill="#d4214d"/></svg>
        0461 738 524
      </li>
      <li>
        <svg viewBox="0 0 20 20" aria-hidden="true"><rect x="2" y="5" width="16" height="11" fill="#d4214d"/><path d="M2 5 L10 11 L18 5" fill="none" stroke="#fff" stroke-width="1.5"/></svg>
        doran@kbtlaw.co
      </li>
      <li>
        <svg viewBox="0 0 20 20" aria-hidden="true"><circle cx="10" cy="10" r="8" fill="#d4214d"/><path d="M6 6 Q9 8 8 11 Q11 12 10 16 M12 4 Q13 7 16 8" fill="none" stroke="#fff" stroke-width="1.5"/></svg>
        www.kbtlaw.co
      </li>
    </ul>
  </section>

  <section class="card card--back">
    <div class="brand">
      <div class="brand__mark"></div>
      <p class="brand__name">KELBRATH<br>BRANT<br>THORNE</p>
    </div>
  </section>
</main>
</body>
</html>
```